Hedge trimming service requires large business signage for side of trailer

Create a signage design for my business, Fernleaf Verge Clipping, a hedge trimming service, which will be used for advertising on a trailer. Design for signage will be created from existing photo supplied.
Dimensions of proposed sign: 600x1200cm
My website: https://www.fernleafvergeclipping.com.au/
Colours we like: green, black, sky blue, white & orange (Kravo logo)
Words to be used with graphic design:
Fernleaf Verge Clipping
Southern Highlands
P Mabel 0417 251 964
W fernleafvergeclipping.com.au
Have your hedges trimmed today!

Fernleaf Verge Clipping/Southern Highlands/Call Mabel 0417 251 964/fernleafvergeclipping.com.au

```html
<!DOCTYPE html>
<html lang="en">
<head>
<meta charset="utf-8">
<title>Fernleaf Verge Clipping – Trailer Sign</title>
<link rel="stylesheet" href="https://fonts.googleapis.com/css2?family=Anton&family=Montserrat:wght@500&family=Poppins:ital,wght@1,800&display=swap">
<style>
  :root {
    --page: #e9e9e9;
    --ink: #0b0b0b;
    --lime: #a9ec2a;
    --lime-soft: #c4f25a;
    --green-mid: #5fb83a;
    --green-deep: #0f6a4e;
    --sky: #cfe0ea;
  }
  * { margin: 0; padding: 0; box-sizing: border-box; }
  html, body { width: 1200px; height: 674px; overflow: hidden; background: var(--page); }
  .sign {
    position: absolute; left: 0; top: 37px; width: 1200px; height: 600px;
    overflow: hidden; background: var(--lime);
  }
  .sign-backdrop, .work-photo { position: absolute; left: 0; top: 0; width: 1200px; height: 600px; }
  .brand {
    position: absolute; left: 540px; width: 580px; top: 56px; text-align: center;
  }
  .brand-dot {
    display: block; width: 46px; height: 46px; border-radius: 50%;
    background: var(--green-deep); margin: 0 auto 10px;
  }
  .brand-name {
    font-family: "Anton", sans-serif; font-size: 42px; line-height: 1;
    color: var(--ink); letter-spacing: 0.2px;
  }
  .brand-region {
    font-family: "Montserrat", sans-serif; font-weight: 500; font-size: 27px;
    color: var(--ink); letter-spacing: 1px; margin-top: 12px;
  }
  .tagline {
    position: absolute; left: 650px; top: 236px; width: 560px; height: 111px;
    background: var(--ink); border-radius: 56px 0 0 56px;
    box-shadow: -3px 4px 0 var(--lime-soft);
    padding-right: 72px; text-align: right;
    font-family: "Anton", sans-serif; font-style: italic; font-size: 40px;
    line-height: 48px; color: var(--lime); display: flex; flex-direction: column;
    justify-content: center; transform-origin: right;
  }
  .tagline span { display: block; transform: skewX(-10deg); }
  .contact {
    position: absolute; display: flex; align-items: center; gap: 12px;
    background: var(--lime); font-family: "Poppins", sans-serif; font-style: italic;
    font-weight: 800; color: var(--ink); box-shadow: 3px 3px 0 var(--ink);
  }
  .contact-web { left: 475px; top: 388px; width: 500px; height: 57px; border-radius: 0 30px 30px 0; padding-left: 32px; font-size: 24px; }
  .contact-phone { left: 886px; top: 448px; width: 330px; height: 58px; border-radius: 30px 0 0 30px; padding-left: 26px; font-size: 27px; }
  .contact svg { flex: none; }
  .grass {
    position: absolute; left: 0; bottom: 0; width: 1200px; height: 58px;
    background: linear-gradient(to bottom, rgba(120,210,50,0) 0%, #7fd037 35%, #4ea524 100%);
  }
</style>
</head>
<body>
<div class="sign">
  <svg class="sign-backdrop" viewBox="0 0 1200 600" aria-hidden="true">
    <defs>
      <linearGradient id="bg" x1="0" y1="0" x2="1" y2="0.3">
        <stop offset="0" stop-color="#0f6a4e"/>
        <stop offset="0.45" stop-color="#5fb83a"/>
        <stop offset="1" stop-color="#a9ec2a"/>
      </linearGradient>
      <radialGradient id="glow" cx="0.72" cy="0.12" r="0.3">
        <stop offset="0" stop-color="#f4ffd8" stop-opacity="0.9"/>
        <stop offset="1" stop-color="#f4ffd8" stop-opacity="0"/>
      </radialGradient>
    </defs>
    <rect width="1200" height="600" fill="url(#bg)"/>
    <path d="M560 310 L1200 60 L1200 140 L560 390 Z" fill="#b6f03c" opacity="0.35"/>
    <path d="M520 430 L1200 240 L1200 290 L520 480 Z" fill="#b6f03c" opacity="0.3"/>
    <rect width="1200" height="600" fill="url(#glow)"/>
    <path d="M375 0 L520 0 C470 160 470 380 510 600 L460 600 C420 380 420 160 375 0 Z" fill="#0f6a4e"/>
    <path d="M320 0 L420 0 C480 180 480 400 470 600 L452 600 C470 380 440 160 320 0 Z" fill="#a9ec2a"/>
  </svg>
  <svg class="work-photo" viewBox="0 0 1200 600" role="img" aria-label="Photo of a hedge trimmer on a ladder and plank cutting back a tall hedge">
    <defs>
      <linearGradient id="photo" x1="0" y1="0" x2="0" y2="1">
        <stop offset="0" stop-color="#cfe0ea"/>
        <stop offset="0.25" stop-color="#6f9a5a"/>
        <stop offset="0.7" stop-color="#4c6a35"/>
        <stop offset="1" stop-color="#5b6f4a"/>
      </linearGradient>
    </defs>
    <path d="M0 0 L320 0 C440 160 470 380 452 600 L0 600 Z" fill="url(#photo)"/>
  </svg>

  <div class="brand">
    <span class="brand-dot" aria-hidden="true"></span>
    <h1 class="brand-name">Fernleaf Verge Clipping</h1>
    <p class="brand-region">SOUTHERN HIGHLANDS</p>
  </div>

  <p class="tagline"><span>HAVE YOUR HEDGES</span><span>TRIMMED TODAY!</span></p>

  <a class="contact contact-web">
    <svg width="22" height="22" viewBox="0 0 24 24" aria-hidden="true">
      <circle cx="12" cy="12" r="11" fill="#0b0b0b"/>
      <g fill="none" stroke="#a9ec2a" stroke-width="1.4">
        <circle cx="12" cy="12" r="6.5"/>
        <ellipse cx="12" cy="12" rx="3" ry="6.5"/>
        <path d="M5.5 12 H18.5 M6.5 9 H17.5 M6.5 15 H17.5"/>
      </g>
    </svg>
    www.fernleafvergeclipping.com.au
  </a>

  <a class="contact contact-phone">
    <svg width="26" height="26" viewBox="0 0 24 24" aria-hidden="true">
      <circle cx="12" cy="12" r="12" fill="#0b0b0b"/>
      <path d="M8.3 6.2 L10 8.6 L8.9 10.2 C9.7 11.9 11.1 13.4 12.9 14.3 L14.5 13.2 L16.9 14.9 L16 17.2 C11.5 17.4 6.6 12.5 6.6 7.4 Z" fill="#a9ec2a"/>
    </svg>
    0417 251 964
  </a>

  <div class="grass" role="img" aria-label="Band of illustrated lawn grass along the bottom edge"></div>
</div>
</body>
</html>
```